Business card for medical clinic

I need an upmarket, modern medical/health business card for my clinic

Contact Information for Business Card

name, address, email, qr code

```html
<!DOCTYPE html>
<html lang="en">
<head>
<meta charset="utf-8">
<title>Meridian Care Clinic – Business Card</title>
<link href="https://fonts.googleapis.com/css2?family=Cinzel:wght@600&family=Arimo:wght@400&display=swap" rel="stylesheet">
<style>
  :root {
    --backdrop: #1e1e1f;
    --blue-deep: #1b5e8c;
    --blue-bright: #1a96d2;
    --blue-ink: #1f6fa8;
    --navy: #1b2d55;
    --sky: #29a8e0;
    --ink: #2b2b2b;
    --paper: #ffffff;
  }
  * { box-sizing: border-box; margin: 0; padding: 0; }
  html, body {
    width: 1200px; height: 900px; overflow: hidden;
    background: var(--backdrop);
  }
  .canvas { position: relative; width: 1200px; height: 900px; }

  .card {
    position: absolute;
    width: 640px; height: 366px;
    border-radius: 16px;
    overflow: hidden;
    box-shadow: 0 14px 30px rgba(0,0,0,.55);
  }

  /* Front */
  .card--front {
    left: 110px; top: 70px;
    background: linear-gradient(100deg, var(--blue-deep) 0%, #1b74a6 55%, var(--blue-bright) 100%);
    display: flex; align-items: center; justify-content: center;
  }
  .brand { display: flex; align-items: center; gap: 18px; }
  .brand__dot {
    width: 64px; height: 64px; border-radius: 50%;
    border: 4px solid currentColor;
    flex: none;
  }
  .brand__name {
    font-family: "Cinzel", serif; font-weight: 600;
    font-size: 30px; letter-spacing: 1.5px; line-height: 1.15;
    white-space: nowrap;
  }
  .card--front .brand { color: var(--paper); }

  /* Back */
  .card--back {
    left: 450px; top: 470px;
    background: var(--paper);
  }
  .card--back::after {
    content: ""; position: absolute; left: 0; right: 0; bottom: 0; height: 12px;
    background: linear-gradient(90deg, var(--navy), var(--sky));
  }
  .card--back .brand {
    position: absolute; left: 28px; top: 160px; width: 268px; gap: 10px;
    color: var(--blue-ink);
  }
  .card--back .brand__dot { width: 40px; height: 40px; border-width: 3px; }
  .card--back .brand__name { font-size: 16px; letter-spacing: 0.8px; }

  .divider {
    position: absolute; left: 320px; top: 70px;
    width: 1.5px; height: 210px; background: var(--blue-ink);
  }
  .contact {
    position: absolute; left: 344px; top: 66px; width: 280px;
    font-family: "Arimo", sans-serif; color: var(--ink);
  }
  .contact__name {
    font-family: "Cinzel", serif; font-weight: 600;
    font-size: 24px; color: var(--blue-ink); letter-spacing: 1px; line-height: 1;
  }
  .contact__role { font-size: 14px; margin-top: 2px; }
  .contact__address { font-size: 14px; line-height: 1.3; margin-top: 18px; }
  .contact__lines { list-style: none; margin-top: 16px; font-size: 14px; }
  .contact__lines li { display: flex; align-items: center; gap: 8px; margin-bottom: 6px; white-space: nowrap; }
  .contact__icon { width: 12px; height: 12px; fill: var(--blue-ink); flex: none; }
</style>
</head>
<body>
<main class="canvas">

  <section class="card card--front" aria-label="Card front">
    <div class="brand">
      <span class="brand__dot"></span>
      <span class="brand__name">Meridian Care Clinic</span>
    </div>
  </section>

  <section class="card card--back" aria-label="Card back">
    <div class="brand">
      <span class="brand__dot"></span>
      <span class="brand__name">Meridian Care Clinic</span>
    </div>

    <span class="divider"></span>

    <div class="contact">
      <p class="contact__name">Daniel Hale</p>
      <p class="contact__role">Director/Founder</p>
      <p class="contact__address">1870 Harbor Lane<br>Westfield CA 90210</p>
      <ul class="contact__lines">
        <li>
          <svg class="contact__icon" viewBox="0 0 24 24" aria-hidden="true"><path d="M6.6 10.8a15.2 15.2 0 0 0 6.6 6.6l2.2-2.2a1 1 0 0 1 1-.25 11.4 11.4 0 0 0 3.6.57 1 1 0 0 1 1 1V20a1 1 0 0 1-1 1A17 17 0 0 1 3 4a1 1 0 0 1 1-1h3.5a1 1 0 0 1 1 1c0 1.25.2 2.45.57 3.57a1 1 0 0 1-.25 1z"/></svg>
          0555 310 4478
        </li>
        <li>
          <svg class="contact__icon" viewBox="0 0 24 24" aria-hidden="true"><path d="M2 5h20v14H2zm2 2v.5l8 5 8-5V7zm0 2.9V17h16V9.9l-8 5z"/></svg>
          hello@meridiancareclinic.com
        </li>
        <li>
          <svg class="contact__icon" viewBox="0 0 24 24" aria-hidden="true"><circle cx="12" cy="12" r="10"/></svg>
          www.meridiancareclinic.com
        </li>
      </ul>
    </div>
  </section>

</main>
</body>
</html>
```